MRT Property - Business Cards

Looking for a business card & general letterhead, signage etc design for our new logo.

Colours:
000a20
0056a2
00b5ef
0088ce
68cef2

Fonts:
Poppins
Karla

Please keep look and feel of new brand - example in the zip package I sent.

```html
<!DOCTYPE html>
<html lang="en">
<head>
<meta charset="utf-8">
<title>MRT Property – Business Cards</title>
<link href="https://fonts.googleapis.com/css2?family=Montserrat:wght@400;600&family=Delius&display=swap" rel="stylesheet">
<style>
  :root {
    --ink: #000a20;
    --brand-blue: #0056a2;
    --brand-mid: #0088ce;
    --brand-sky: #00b5ef;
    --brand-light: #68cef2;
    --card-back: #0b56a3;
    --paper: #ffffff;
    --backdrop: #e4e1dc;
  }
  html, body {
    margin: 0;
    padding: 0;
    width: 900px;
    height: 1200px;
    overflow: hidden;
    background: var(--backdrop);
    font-family: "Montserrat", sans-serif;
  }
  .canvas {
    position: relative;
    width: 900px;
    height: 1200px;
  }
  .card {
    position: absolute;
    border-radius: 24px;
    box-shadow: 0 6px 14px rgba(0, 10, 32, 0.25);
  }
  .card-front {
    left: 80px; top: 131px;
    width: 742px; height: 440px;
    background: var(--paper);
  }
  .card-back {
    left: 78px; top: 638px;
    width: 744px; height: 440px;
    background: var(--card-back);
  }
  .brand-mark {
    position: absolute;
    display: flex;
    align-items: center;
    font-family: "Montserrat", sans-serif;
    font-weight: 600;
    white-space: nowrap;
  }
  .brand-dot { border-radius: 50%; flex: none; }
  .card-front .brand-mark {
    left: 70px; top: 203px;
    font-size: 33px;
    color: var(--brand-blue);
    gap: 12px;
  }
  .card-front .brand-dot {
    width: 26px; height: 26px;
    background: var(--brand-blue);
  }
  .card-back .brand-mark {
    left: 110px; top: 180px;
    font-size: 66px;
    color: var(--paper);
    gap: 22px;
  }
  .card-back .brand-dot {
    width: 50px; height: 50px;
    background: var(--paper);
  }
  .divider {
    position: absolute;
    left: 349px; top: 121px;
    width: 2px; height: 224px;
    background: var(--brand-blue);
  }
  .contact {
    position: absolute;
    left: 365px; top: 118px;
    color: var(--ink);
    font-size: 15px;
    line-height: 21px;
  }
  .person-name {
    margin: 0;
    font-family: "Delius", cursive;
    font-weight: 400;
    font-size: 29px;
    line-height: 38px;
    color: var(--brand-blue);
  }
  .person-role { margin: 0 0 22px; }
  .address { margin: 0 0 22px; font-style: normal; }
  .contact-list { list-style: none; margin: 0; padding: 0; }
  .contact-list li {
    display: flex;
    align-items: center;
    gap: 10px;
    height: 28px;
  }
  .contact-list svg { width: 16px; height: 16px; fill: var(--brand-blue); flex: none; }
</style>
</head>
<body>
<main class="canvas">
  <section class="card card-front" aria-label="Business card front">
    <div class="brand-mark"><span class="brand-dot"></span>MRT Property</div>
    <div class="divider"></div>
    <div class="contact">
      <h1 class="person-name">Daniel Harper</h1>
      <p class="person-role">Managing Director</p>
      <address class="address">218 Maple Ridge Ave Suite<br>40 Fairview Ohio 44020</address>
      <ul class="contact-list">
        <li>
          <svg viewBox="0 0 24 24" aria-hidden="true"><path d="M6.6 10.8a15.1 15.1 0 0 0 6.6 6.6l2.2-2.2a1 1 0 0 1 1-.25 11.4 11.4 0 0 0 3.6.57 1 1 0 0 1 1 1V20a1 1 0 0 1-1 1A17 17 0 0 1 3 4a1 1 0 0 1 1-1h3.5a1 1 0 0 1 1 1c0 1.25.2 2.45.57 3.57a1 1 0 0 1-.25 1z"/></svg>
          1 (555) 014-2739
        </li>
        <li>
          <svg viewBox="0 0 24 24" aria-hidden="true"><path d="M2 5h20v14H2z" fill="none"/><path d="M3 6h18v12H3z"/><path d="M3 6l9 7 9-7" fill="none" stroke="#fff" stroke-width="1.8"/></svg>
          hello@mrtproperty.example
        </li>
        <li>
          <svg viewBox="0 0 24 24" aria-hidden="true"><circle cx="12" cy="12" r="10"/><path d="M2 12h20M12 2c3 3 3 17 0 20M12 2c-3 3-3 17 0 20" fill="none" stroke="#fff" stroke-width="1.4"/></svg>
          www.mrtproperty.example
        </li>
      </ul>
    </div>
  </section>

  <section class="card card-back" aria-label="Business card back">
    <div class="brand-mark"><span class="brand-dot"></span>MRT Property</div>
  </section>
</main>
</body>
</html>
```